Residential & commercial cleaning business

Looking for Brazilian colors, green/blue/yellow.
Name of business is “Marlowe’s Cleaning”.
Second side of card will be for ‘confirming customer next appointment date/time.
Want to include in description…residential & commercial cleaning, experienced, highly recommended, reasonable rates, free estimates, Marlowe’sCleaningCo@brightmop.net, Fernwood Falls, NH, Call today at 555.218.6094.

```html
<!DOCTYPE html>
<html lang="en">
<head>
<meta charset="utf-8">
<title>Marlowe’s Cleaning – Business Card</title>
<link href="https://fonts.googleapis.com/css2?family=Montserrat:wght@500;600;700&display=swap" rel="stylesheet">
<style>
  :root {
    --stage: #4d4d4d;
    --leaf: #699a33;
    --sun: #fbe100;
    --paper: #ffffff;
  }
  html, body {
    margin: 0;
    padding: 0;
    width: 1200px;
    height: 1200px;
    overflow: hidden;
    background: var(--stage);
    font-family: "Montserrat", Arial, sans-serif;
  }
  .card {
    position: absolute;
    left: 186px;
    width: 828px;
    height: 460px;
    display: block;
  }
  .card--front { top: 112px; }
  .card--back { top: 628px; }
  .card text { font-family: "Montserrat", Arial, sans-serif; }
  .fill-leaf { fill: var(--leaf); }
  .fill-sun { fill: var(--sun); }
  .fill-paper { fill: var(--paper); }
  .services { font-size: 45px; font-weight: 500; fill: var(--leaf); }
  .brand-name { font-size: 58px; font-weight: 600; fill: var(--leaf); }
  .tagline { font-size: 17px; font-weight: 500; fill: var(--leaf); letter-spacing: 1px; }
  .call-label { font-size: 35px; font-weight: 700; fill: var(--paper); }
  .phone { font-size: 43px; font-weight: 700; fill: var(--leaf); letter-spacing: 1px; }
  .appt-title { font-size: 68px; font-weight: 600; fill: var(--sun); letter-spacing: 1px; }
  .field-label { font-size: 28px; font-weight: 500; fill: var(--leaf); }
  .contact { font-size: 30px; font-weight: 500; fill: var(--paper); letter-spacing: 0.5px; }
</style>
</head>
<body>

<svg class="card card--front" viewBox="0 0 1035 575" aria-label="Card front">
  <rect class="fill-leaf" width="1035" height="575"/>
  <path class="fill-sun" d="M0,0 L975,0 C1040,110 1045,320 1002,420 C965,485 900,487 850,482 C650,458 450,318 250,318 C130,320 50,365 0,396 Z"/>
  <path class="fill-paper" d="M0,0 L940,0 C1005,110 1012,300 975,398 C945,455 900,466 850,464 C650,444 450,302 250,304 C130,306 50,350 0,378 Z"/>

  <text class="services" x="83" y="128">Residential</text>
  <text class="services" x="83" y="173">&amp; Commercial</text>
  <text class="services" x="83" y="218">cleaning</text>

  <g class="brand">
    <text class="brand-name" x="710" y="180" text-anchor="middle">Marlowe’s</text>
    <text class="brand-name" x="710" y="248" text-anchor="middle">Cleaning</text>
  </g>

  <path id="tagline-curve" d="M92,298 C250,262 450,292 650,362 C740,394 800,414 860,422" fill="none"/>
  <text class="tagline">
    <textPath href="#tagline-curve">EXPERIENCED · HIGHLY RECOMMENDED · REASONABLE RATES · FREE ESTIMATES</textPath>
  </text>

  <text class="call-label" x="255" y="393" text-anchor="middle">Call today at</text>
  <rect class="fill-sun" x="64" y="410" width="384" height="102" rx="51"/>
  <text class="phone" x="265" y="476" text-anchor="middle">555.218.6094</text>
</svg>

<svg class="card card--back" viewBox="0 0 1035 575" aria-label="Card back">
  <rect class="fill-leaf" width="1035" height="575"/>
  <text class="appt-title" x="517.5" y="155" text-anchor="middle">Your next appointment</text>

  <rect class="fill-sun" x="86" y="229" width="402" height="77" rx="38.5"/>
  <text class="field-label" x="117" y="277">Date:</text>

  <rect class="fill-sun" x="541" y="229" width="402" height="77" rx="38.5"/>
  <text class="field-label" x="578" y="277">Time:</text>

  <rect class="fill-sun" x="86" y="335" width="857" height="77" rx="38.5"/>
  <text class="field-label" x="117" y="384">Details:</text>

  <text class="contact" x="517.5" y="457" text-anchor="middle">Fernwood Falls, NH</text>
  <text class="contact" x="517.5" y="498" text-anchor="middle">Marlowe’sCleaningCo@brightmop.net</text>
</svg>

</body>
</html>
```